Storm Restoration Contractor needs a professional letterhead design

Looking for a professional letterhead design. Not looking for your cheapo MS Word standard ones that are readily available. Dont want it to be cookie cutter look like ones readily available online. We just recently changed our logo and want to freshen up all our documents. Our company handles restoring a property back to a pre-loss condition after a storm damages it. For example, wind, hail, flood, fire losses.

Target Market(s)

Property Owners, Homeowners, Property Owners, Commercial Property Owners, Property Management Companies

Industry/Entity Type

Construction Company

Requirements
Must have
• Professional, Use 1 of 2 logo options
• Storm Restoration, Roofing, Siding, Windows

```html
<!DOCTYPE html>
<html lang="en">
<head>
<meta charset="utf-8">
<title>Northgate Exteriors Letterhead</title>
<link rel="stylesheet" href="https://fonts.googleapis.com/css2?family=Jost:wght@400;600&display=swap">
<style>
  :root {
    --backdrop: #e6e6e6;
    --paper: #ffffff;
    --brand-blue: #1f74c2;
    --brand-grey: #4a4a4c;
    --faint-blue: #eef1f8;
    --on-blue: #ffffff;
  }
  * { margin: 0; padding: 0; box-sizing: border-box; }
  html, body {
    width: 1200px; height: 795px; overflow: hidden;
    background: var(--backdrop);
    font-family: "Jost", sans-serif;
  }
  .canvas {
    position: relative; width: 1200px; height: 795px;
    display: flex; align-items: center; justify-content: center;
  }
  .letterhead {
    position: relative; width: 500px; height: 707px;
    background: var(--paper);
    box-shadow: 0 6px 22px rgba(0,0,0,0.12);
    overflow: hidden;
  }
  .letterhead__art { position: absolute; inset: 0; width: 100%; height: 100%; }
  .brand {
    position: absolute; left: 24px; top: 42px;
    display: flex; align-items: center; gap: 8px;
  }
  .brand__dot {
    width: 28px; height: 28px; border-radius: 50%;
    border: 3px solid var(--brand-blue); flex: none;
  }
  .brand__name {
    font-weight: 600; font-size: 16px; letter-spacing: 1.5px;
    color: var(--brand-blue); text-transform: uppercase; line-height: 1.05;
    padding-left: 8px; border-left: 1px solid var(--brand-blue);
  }
  .brand__name span { display: block; }
  .website {
    position: absolute; right: 26px; top: 22px;
    font-size: 10px; color: var(--brand-blue); letter-spacing: 0.3px;
  }
  .contact {
    position: absolute; left: 30px; bottom: 20px;
    color: var(--on-blue); font-size: 10.5px; line-height: 1.5;
  }
  .contact__row { display: flex; align-items: center; gap: 4px; }
  .contact__icon { width: 9px; height: 9px; fill: var(--on-blue); }
  .contact__gap { width: 6px; }
</style>
</head>
<body>
<main class="canvas">
  <article class="letterhead">
    <svg class="letterhead__art" viewBox="0 0 500 707" preserveAspectRatio="none" aria-hidden="true">
      <!-- header swooshes -->
      <path d="M0 106 C140 102 210 80 260 40 C285 18 305 4 330 0 L342 0 C316 6 296 20 270 44 C218 90 146 114 0 116 Z" fill="var(--brand-blue)"/>
      <path d="M0 124 C150 120 225 92 275 48 C305 20 330 4 360 0" fill="none" stroke="var(--brand-grey)" stroke-width="2.5"/>
      <!-- faint background mark -->
      <circle cx="250" cy="330" r="118" fill="none" stroke="var(--faint-blue)" stroke-width="14"/>
      <!-- footer band -->
      <path d="M0 707 L0 628 C100 624 200 612 290 586 C380 560 440 536 500 522 L500 707 Z" fill="var(--brand-blue)"/>
      <path d="M0 618 C100 614 200 602 290 576 C380 550 440 526 500 512" fill="none" stroke="var(--brand-grey)" stroke-width="3"/>
      <path d="M0 610 C100 606 200 594 288 568 C378 542 438 518 500 503" fill="none" stroke="var(--brand-blue)" stroke-width="1.5"/>
    </svg>

    <header class="brand">
      <span class="brand__dot"></span>
      <span class="brand__name"><span>Northgate</span><span>Exteriors</span></span>
    </header>

    <p class="website">www.northgateexteriors.com</p>

    <footer class="contact">
      <p>Northgate Exteriors</p>
      <p>2250 Harbor Lane, Millbrook, CA 95010</p>
      <p class="contact__row">
        <svg class="contact__icon" viewBox="0 0 10 10"><path d="M2 0.5 L4 2.8 L3 4 C3.6 5.3 4.7 6.4 6 7 L7.2 6 L9.5 8 L8.2 9.5 C4.5 9.2 0.8 5.5 0.5 1.8 Z"/></svg>
        <span>(555) 014-2278</span><span class="contact__gap"></span>
        <svg class="contact__icon" viewBox="0 0 10 10"><rect x="2" y="0.5" width="6" height="3"/><rect x="0.5" y="4" width="9" height="5.5" rx="1"/></svg>
        <span>(555) 014-2279</span><span class="contact__gap"></span>
        <svg class="contact__icon" viewBox="0 0 10 10"><path d="M0.5 2 H9.5 V8.5 H0.5 Z M0.5 2 L5 5.8 L9.5 2"/></svg>
        <span>info@northgateexteriors.com</span>
      </p>
    </footer>
  </article>
</main>
</body>
</html>
```